Market Research firm needs updated business cards with new logo

We need the logo to be included somewhere on the card (attached). We would also like the phrases "Independent, Objective, Comprehensive" and "Research You Can Trust" somewhere on the card. Front or back. Our colors are hex codes 6075a7, e48d25 and 5a5b5b. Though you are certainly not limited to those shades, whatever you produce should coordinate with them. I have also attached our favicon. Feel free to use it in your design, but please do not use it to replace the full logo.

Contact Information for Business Card

see project description

Font styles to use
Other font styles liked:
• Open Sans

Requirements
Must have
• the logo
• We use Open Sans font

```html
<!DOCTYPE html>
<html lang="en">
<head>
<meta charset="utf-8">
<title>Corvane Insight – Business Cards</title>
<link rel="stylesheet" href="https://fonts.googleapis.com/css2?family=EB+Garamond:wght@400&family=Open+Sans:wght@400;600&family=Roboto:wght@300;700&display=swap">
<style>
  :root {
    --bg: #555352;
    --orange: #e48d25;
    --orange-dark: #c97a1c;
    --slate: #5a5b5b;
    --white: #ffffff;
    --ink: #3f4040;
  }
  * { box-sizing: border-box; margin: 0; padding: 0; }
  html, body { width: 1200px; height: 960px; overflow: hidden; }
  body {
    background: var(--bg);
    font-family: "Open Sans", sans-serif;
    position: relative;
  }
  .card {
    position: absolute;
    width: 700px;
    height: 400px;
    background: var(--white);
    overflow: hidden;
    box-shadow: 0 10px 24px rgba(0,0,0,.35);
  }
  /* Back card */
  .card-back { left: 110px; top: 80px; }
  .card-back .band {
    position: absolute; left: 0; width: 100%;
    background: var(--orange);
  }
  .card-back .band-top { top: 0; height: 96px; }
  .card-back .band-bottom { bottom: 0; height: 96px; }
  .wordmark {
    position: absolute;
    display: flex; align-items: center; gap: 12px;
    font-family: "Open Sans", sans-serif;
    font-weight: 600;
    color: var(--slate);
    white-space: nowrap;
  }
  .wordmark .dot {
    border-radius: 50%;
    background: var(--orange);
  }
  .card-back .wordmark { left: 50%; top: 50%; transform: translate(-50%, -50%); font-size: 46px; }
  .card-back .wordmark .dot { width: 34px; height: 34px; }

  /* Front card */
  .card-front { left: 390px; top: 480px; }
  .card-front .panel { position: absolute; inset: 0; }
  .card-front .wordmark { left: 60px; top: 108px; font-size: 30px; }
  .card-front .wordmark .dot { width: 22px; height: 22px; }
  .tagline {
    position: absolute; right: 36px; top: 34px;
    font-family: "EB Garamond", serif;
    font-size: 17px; line-height: 1.25;
    color: var(--ink);
    text-align: center;
  }
  .person {
    position: absolute; left: 60px; top: 292px;
    padding-left: 16px;
    border-left: 6px solid var(--orange);
    font-family: "Roboto", sans-serif;
    color: var(--white);
  }
  .person .name { font-weight: 700; font-size: 28px; letter-spacing: .3px; line-height: 1.1; }
  .person .role { font-weight: 300; font-size: 21px; letter-spacing: .3px; }
  .contact {
    position: absolute; right: 0;
    width: 270px; height: 56px;
    background: var(--orange);
    clip-path: polygon(14px 0, 100% 0, 100% 100%, 0 100%);
    display: flex; align-items: center; gap: 14px;
    padding-left: 22px;
    font-family: "Roboto", sans-serif;
    font-size: 14px; line-height: 1.3;
    color: var(--white);
  }
  .contact-phone { top: 150px; }
  .contact-web { top: 216px; }
  .contact-address { top: 282px; }
  .contact .icon {
    flex: none; width: 36px; height: 36px; border-radius: 50%;
    background: var(--orange-dark);
    box-shadow: 0 2px 4px rgba(0,0,0,.25);
    display: flex; align-items: center; justify-content: center;
  }
</style>
</head>
<body>
  <section class="card card-back" aria-label="Card back">
    <div class="band band-top"></div>
    <div class="wordmark"><span class="dot"></span>Corvane Insight</div>
    <div class="band band-bottom"></div>
  </section>

  <section class="card card-front" aria-label="Card front">
    <svg class="panel" width="700" height="400" viewBox="0 0 700 400" aria-hidden="true">
      <polygon points="0,232 700,130 700,400 0,400" fill="#5a5b5b"/>
    </svg>
    <div class="wordmark"><span class="dot"></span>Corvane Insight</div>
    <p class="tagline">Careful, Impartial<br>Thorough and Clear<br>Findings You Can Rely On</p>

    <div class="person">
      <div class="name">MARLOWE KEANE</div>
      <div class="role">SOLUTION MANAGER</div>
    </div>

    <div class="contact contact-phone">
      <span class="icon">
        <svg width="18" height="18" viewBox="0 0 24 24"><path fill="#fff" d="M6.6 10.8a15.1 15.1 0 0 0 6.6 6.6l2.2-2.2c.3-.3.7-.4 1-.2 1.1.4 2.3.6 3.6.6.6 0 1 .4 1 1V20c0 .6-.4 1-1 1A17 17 0 0 1 3 4c0-.6.4-1 1-1h3.5c.6 0 1 .4 1 1 0 1.3.2 2.5.6 3.6.1.3 0 .7-.2 1z"/></svg>
      </span>
      <span>+1555 014 2206<br>+1555 017 5645</span>
    </div>
    <div class="contact contact-web">
      <span class="icon">
        <svg width="18" height="18" viewBox="0 0 24 24" fill="none" stroke="#fff" stroke-width="1.8"><circle cx="12" cy="12" r="9"/><ellipse cx="12" cy="12" rx="4" ry="9"/><path d="M3 12h18M5 7h14M5 17h14"/></svg>
      </span>
      <span>www.northfieldstudio.com<br>www.northfield.com</span>
    </div>
    <div class="contact contact-address">
      <span class="icon">
        <svg width="16" height="18" viewBox="0 0 24 24"><path fill="#fff" d="M12 2a7 7 0 0 0-7 7c0 5 7 13 7 13s7-8 7-13a7 7 0 0 0-7-7zm0 9.5A2.5 2.5 0 1 1 12 6.5a2.5 2.5 0 0 1 0 5z"/></svg>
      </span>
      <span>12 Harbor Lane,<br>Eastgate</span>
    </div>
  </section>
</body>
</html>
```